New Fun, Positive, energised looking Business Card Needed for High Achiever Coach

I am looking for a two sided full colour business card. I am self employed and have recently re branded my 1-2-1 work Renewing Driven Leaders. My target client base for these cards is therefore high achievers - usually aged 40 -55, they are often entrepreneurs, CEO or work in banking and finance and 2/3 are male. I work with them on 90 day or 6 month coaching programs to help them live their success in a healthier, more sustainable and fulfiiled way. They pay for this privately so though they are corporate types the cards need not look 'corporate'. I want to portray the idea of transformation, vitality and re-connecting.
You can get a feel for the look I like on my new website: morvenlisk.co.uk
I want to use this logo with strapline (Renewing Driven Leaders) (I purchased off Logoharbor) and font/ colours (the turquoise and green).
Details to include on the card:
www.morvenlisk.co.uk
+44 7915 302618
morven@morvenlisk.co.uk
skype: morvenlisk
I'd also like to include:
Do you struggle to switch off? Want to be healthier and feel fitter? Want closer relationships? More clarity over the direction you are headed? I can help you do these things using integrated mind-body techniques. Visit morvenlisk.co.uk TODAY to apply for a FREE Discovery session.
BUT if that is too much text for a card I am open to advice/ammendments.
Updates
Thanks for your design - I am considering them. PLease change the wording to :

```html
<!DOCTYPE html>
<html lang="en">
<head>
<meta charset="utf-8">
<title>Morven Lisk – Business Card</title>
<link rel="stylesheet" href="https://fonts.googleapis.com/css2?family=Open+Sans:wght@400;600;700;800&display=swap">
<style>
  :root {
    --turquoise: #14a6cb;
    --green: #5cb865;
    --ink: #333333;
    --divider: #d6d6d6;
    --card: #ffffff;
    --backdrop: #e9e9ee;
  }
  * { box-sizing: border-box; margin: 0; padding: 0; }
  html, body { width: 1200px; height: 987px; overflow: hidden; }
  body {
    background: var(--backdrop);
    font-family: "Open Sans", Arial, sans-serif;
    color: var(--ink);
    position: relative;
  }
  .card {
    position: absolute;
    left: 190px;
    width: 820px;
    height: 440px;
    background: var(--card);
    border-radius: 28px;
    overflow: hidden;
    box-shadow: 0 6px 18px rgba(0,0,0,0.12);
  }
  .card--front { top: 36px; }
  .card--back { top: 511px; }

  .brand {
    position: absolute;
    left: 60px;
    top: 120px;
    width: 300px;
    text-align: center;
  }
  .card--back .brand { top: 130px; }
  .brand__mark {
    width: 54px; height: 54px;
    border-radius: 50%;
    background: var(--green);
    margin: 0 auto 14px;
  }
  .brand__name {
    font-size: 46px;
    font-weight: 800;
    color: var(--turquoise);
    line-height: 1;
    letter-spacing: 0.5px;
  }
  .brand__tagline {
    margin-top: 10px;
    font-size: 17px;
    color: var(--turquoise);
    font-weight: 400;
  }

  .divider {
    position: absolute;
    left: 405px;
    width: 1px;
    background: var(--divider);
  }
  .card--front .divider { top: 120px; height: 170px; }
  .card--back .divider { top: 60px; height: 320px; }

  .contact {
    position: absolute;
    left: 440px;
    top: 140px;
    list-style: none;
    font-size: 25px;
    line-height: 44px;
  }
  .contact li { display: flex; align-items: center; gap: 10px; }
  .contact svg { width: 22px; height: 22px; flex: none; }

  .bands { position: absolute; left: 0; bottom: 0; width: 820px; height: 130px; }
  .web {
    position: absolute;
    right: 60px;
    bottom: 22px;
    font-size: 30px;
    color: #ffffff;
    letter-spacing: 2px;
  }

  .pitch {
    position: absolute;
    left: 440px;
    top: 70px;
    width: 350px;
    font-size: 18px;
    line-height: 28px;
  }
  .pitch p + p { margin-top: 10px; }
  .pitch strong { font-weight: 700; }
</style>
</head>
<body>

<section class="card card--front" aria-label="Business card front">
  <div class="brand">
    <div class="brand__mark"></div>
    <div class="brand__name">Morven Lisk</div>
    <div class="brand__tagline">Renewing Driven Leaders</div>
  </div>
  <div class="divider"></div>
  <ul class="contact">
    <li>
      <svg viewBox="0 0 22 22" aria-hidden="true"><circle cx="11" cy="11" r="9.5" fill="none" stroke="#14a6cb" stroke-width="2"/><path d="M7.5 6.5l2 0 1 2.5-1.3 1a6 6 0 0 0 2.8 2.8l1-1.3 2.5 1v2a1.5 1.5 0 0 1-1.5 1.5A8 8 0 0 1 6 8a1.5 1.5 0 0 1 1.5-1.5z" fill="#14a6cb"/></svg>
      +44 7915 302618
    </li>
    <li>
      <svg viewBox="0 0 22 22" aria-hidden="true"><rect x="2" y="5" width="18" height="13" rx="2" fill="#14a6cb"/><path d="M3 6.5l8 6 8-6" fill="none" stroke="#fff" stroke-width="1.6"/></svg>
      morven@morvenlisk.co.uk
    </li>
    <li>
      <svg viewBox="0 0 22 22" aria-hidden="true"><circle cx="11" cy="11" r="10" fill="#14a6cb"/></svg>
      morvenlisk
    </li>
  </ul>
  <svg class="bands" viewBox="0 0 820 130" aria-hidden="true">
    <polygon points="0,0 330,0 355,28 0,28" fill="#5cb865"/>
    <polygon points="0,40 345,40 370,62 820,62 820,130 0,130" fill="#14a6cb"/>
  </svg>
  <div class="web">www.morvenlisk.co.uk</div>
</section>

<section class="card card--back" aria-label="Business card back">
  <div class="brand">
    <div class="brand__mark"></div>
    <div class="brand__name">Morven Lisk</div>
    <div class="brand__tagline">Renewing Driven Leaders</div>
  </div>
  <div class="divider"></div>
  <div class="pitch">
    <p>Do you find it hard to unwind?<br>Want more energy and better health?<br>Want stronger connections?<br>A clearer sense of where you are going?</p>
    <p>I can guide you there with joined-up mind-body methods.</p>
    <p>Visit <strong>morvenlisk.co.uk</strong> TODAY to book a FREE Discovery session.</p>
  </div>
</section>

</body>
</html>
```